Thornvale Group needs a business card design

We need a new business card design using the logo recently selected in a logo competition on Pixel Bazaar. Our business is a consultancy specializing in aviation and energy and the winning business card design will promote an image of precision and professionalism with creativity.

Please use the logo with the name on the front of the card and use a complementary font. Make the back white with either the light grey or dark grey logo.

Target Market(s)

Senior finance and legal leaders at aviation and energy companies

Industry/Entity Type

Management Consulting

Contact Information for Business Card

Peter Castrell
President
Thornvale Group

www.thornvalegroup.example

(555) 204-6391
pc@thornvalegroup.example

Requirements
Must have
• Professional font that goes well with the logo font

```html
<!DOCTYPE html>
<html lang="en">
<head>
<meta charset="utf-8">
<title>Thornvale Group — Business Card</title>
<link href="https://fonts.googleapis.com/css2?family=Open+Sans:wght@400;600;700&display=swap" rel="stylesheet">
<style>
  :root {
    --canvas-bg: #e9ebee;
    --card-white: #ffffff;
    --navy: #1f4f7d;
    --navy-deep: #0d2c4e;
    --blue-top: #2f7aa3;
    --blue-bottom: #082a4c;
    --grey-text: #8a96a3;
    --divider: #d7dde3;
    --shadow: rgba(10, 30, 50, 0.18);
  }
  * { box-sizing: border-box; margin: 0; padding: 0; }
  html, body {
    width: 1200px;
    height: 913px;
    overflow: hidden;
    background: var(--canvas-bg);
    font-family: "Open Sans", Arial, sans-serif;
  }
  .canvas {
    position: relative;
    width: 1200px;
    height: 913px;
  }
  .card {
    position: absolute;
    width: 560px;
    height: 320px;
    border-radius: 4px;
    box-shadow: 0 10px 28px var(--shadow);
    overflow: hidden;
  }

  /* Contact side */
  .card--contact {
    left: 70px;
    top: 130px;
    background: var(--card-white);
    display: flex;
    align-items: center;
  }
  .card__brand {
    width: 270px;
    display: flex;
    justify-content: center;
  }
  .wordmark {
    font-weight: 600;
    color: var(--navy);
    letter-spacing: 0.08em;
    text-transform: uppercase;
  }
  .card--contact .wordmark { font-size: 22px; }
  .card__divider {
    width: 1px;
    height: 150px;
    background: var(--divider);
  }
  .card__details {
    padding-left: 30px;
    flex: 1;
  }
  .person__name {
    font-size: 22px;
    font-weight: 700;
    color: var(--navy);
    line-height: 1.1;
  }
  .person__title {
    font-size: 13px;
    color: var(--grey-text);
    margin: 2px 0 22px 20px;
  }
  .contact-list { list-style: none; }
  .contact-list li {
    display: flex;
    align-items: center;
    gap: 8px;
    font-size: 13px;
    color: var(--navy);
    line-height: 1.55;
  }
  .contact-list svg {
    width: 11px;
    height: 11px;
    fill: none;
    stroke: var(--grey-text);
    stroke-width: 1.6;
    flex: none;
  }

  /* Brand side */
  .card--brand {
    left: 570px;
    top: 470px;
    background: linear-gradient(160deg, var(--blue-top) 0%, var(--navy) 45%, var(--blue-bottom) 100%);
    display: flex;
    align-items: center;
    justify-content: center;
  }
  .card--brand .wordmark {
    color: #ffffff;
    font-size: 34px;
    font-weight: 600;
  }
</style>
</head>
<body>
  <main class="canvas">
    <section class="card card--contact" aria-label="Business card, contact side">
      <div class="card__brand">
        <span class="wordmark">Thornvale Group</span>
      </div>
      <div class="card__divider"></div>
      <div class="card__details">
        <h1 class="person__name">Peter Castrell</h1>
        <p class="person__title">President</p>
        <ul class="contact-list">
          <li>
            <svg viewBox="0 0 12 12" aria-hidden="true"><path d="M3 1 L5 3.5 L3.8 4.8 Q5 7.2 7.2 8.2 L8.5 7 L11 9 L9.5 11 Q4.5 10.5 1 3 Z"/></svg>
            (555) 204-6391
          </li>
          <li>
            <svg viewBox="0 0 12 12" aria-hidden="true"><rect x="1" y="2.5" width="10" height="7"/><path d="M1 2.5 L6 6.5 L11 2.5"/></svg>
            pc@thornvalegroup.example
          </li>
          <li>
            <svg viewBox="0 0 12 12" aria-hidden="true"><circle cx="6" cy="6" r="5"/><path d="M1 6 H11 M6 1 Q3 6 6 11 Q9 6 6 1"/></svg>
            www.thornvalegroup.example
          </li>
        </ul>
      </div>
    </section>

    <section class="card card--brand" aria-label="Business card, brand side">
      <span class="wordmark">Thornvale Group</span>
    </section>
  </main>
</body>
</html>
```